Sales sheet for printing and embroidery apparel items - Copper Hollow Graphics

I would like a one page flyer or sales sheet that I would use as a template to send different images of apparel we produce. I have attached examples of layouts I like.
- Ideally, it would have space for 3-5 items.
- I would like it one page only - not a folding flyer.
- Our companies name is Copper Hollow Graphics.
- This will be used for many different products and markets so I don't need wording/copy. You can use wording from the 7M9 or T58 flyer.

Colors
0054AA
0677BA
7BADD7
CADEEF
E8F1F8
00AB8E
00BBA5
67D7C9
C6EFE9
E9F9F6
FFC000
F8CF3A
FAE287
FDF2CF
FEFAEE

Requirements
Must have
• Places for between 3 and 5 images of apparel (t-shirts, hats etc)

```html
<!DOCTYPE html>
<html lang="en">
<head>
<meta charset="utf-8">
<title>Copper Hollow Graphics – Sample Merch Kit</title>
<link href="https://fonts.googleapis.com/css2?family=Roboto:ital,wght@0,400;0,500;0,700;0,900;1,400&family=Roboto+Condensed:wght@700&display=swap" rel="stylesheet">
<style>
  :root{
    --blue-deep:#0054AA;
    --blue-mid:#0677BA;
    --blue-soft:#7BADD7;
    --blue-pale:#CADEEF;
    --green-deep:#00AB8E;
    --green-mid:#00BBA5;
    --green-soft:#67D7C9;
    --gold:#FFC000;
    --gold-soft:#F8CF3A;
    --gold-pale:#FDF2CF;
    --coral:#ef5d5d;
    --red:#e3262b;
    --backdrop:#3875fb;
    --paper:#ffffff;
    --ink:#111111;
    --shirt-olive:#5e5a40;
    --shirt-black:#0c0c0c;
    --shirt-blue:#2a35a8;
  }
  *{box-sizing:border-box;margin:0;padding:0}
  html,body{width:1200px;height:2521px;overflow:hidden}
  body{background:var(--backdrop);font-family:"Roboto",Arial,sans-serif;color:var(--ink);position:relative}

  .sheet{position:absolute;left:188px;top:727px;width:824px;height:1067px;background:var(--paper);overflow:hidden;box-shadow:0 18px 40px rgba(0,0,0,.25)}
  .bands{position:absolute;left:0;top:0;width:824px;height:1067px}

  .brand-name{position:absolute;left:42px;top:44px;font-weight:900;font-size:44px;line-height:1.05;color:var(--blue-deep);text-transform:uppercase;letter-spacing:.3px}
  .kit-title{position:absolute;left:124px;top:182px;font-family:"Roboto Condensed","Roboto",sans-serif;font-weight:700;font-size:22px;line-height:1;color:var(--ink)}
  .badge{position:absolute;left:567px;top:51px;width:110px;height:98px;background:var(--blue-deep)}
  .est{position:absolute;left:567px;top:155px;font-weight:700;font-size:26px;line-height:1;color:var(--blue-deep)}

  .spec{position:absolute;top:326px;font-size:24px;line-height:1;color:#222}
  .spec b{color:var(--red);font-weight:500}
  .spec.model{left:54px}
  .spec.series{left:385px}
  .warning{position:absolute;left:54px;top:370px;font-size:12.5px;line-height:1;color:#222;display:flex;align-items:center;gap:7px}
  .warning span{background:var(--red);color:#fff;font-weight:500;font-size:11px;padding:2px 7px;border-radius:8px}

  .garment{position:absolute;top:436px;height:230px;border-radius:16px 16px 6px 6px}
  .garment.olive{left:35px;width:236px;background:var(--shirt-olive)}
  .garment.black{left:296px;width:236px;background:var(--shirt-black)}
  .garment.blue{left:556px;width:236px;background:var(--shirt-blue)}
  .garment-shadow{position:absolute;top:668px;width:180px;height:22px;border-radius:50%;background:radial-gradient(closest-side,rgba(0,0,0,.18),rgba(0,0,0,0))}

  .kit-contents{position:absolute;left:36px;top:710px;width:204px;height:216px;background:var(--coral);border-radius:8px;padding:16px 22px;color:#fff}
  .kit-contents h2{font-weight:700;font-size:27px;line-height:1.08}
  .kit-contents ol{list-style:none;margin-top:20px;font-size:14.5px;line-height:23.5px}

  .order-steps{position:absolute;left:247px;top:710px;width:541px;height:216px;background:var(--blue-deep);border-radius:8px;padding:16px 20px;color:#fff}
  .order-steps h2{font-weight:500;font-size:22px;line-height:1}
  .order-steps .sub{font-size:14.5px;line-height:1.2;margin-top:3px}
  .step{position:relative;padding-left:32px;margin-top:11px;font-size:9.3px;line-height:1.55}
  .step strong{display:block;font-weight:700}
  .step svg{position:absolute;left:0;top:2px}

  .about{position:absolute;left:40px;top:955px;width:392px}
  .about h2{font-weight:700;font-size:20px;line-height:1}
  .about p{font-size:7.6px;line-height:1.3;margin-top:7px}
  .about .fine{font-weight:700;display:block}

  .contact{position:absolute;right:39px;top:958px;text-align:right}
  .contact .pill{display:inline-block;background:var(--blue-deep);color:#fff;font-weight:700;font-size:18px;line-height:27px;letter-spacing:.6px;padding:0 12px;border-radius:14px}
  .contact .phone{font-weight:700;font-size:27px;line-height:1;margin-top:10px}
  .contact .web{font-size:17px;line-height:1;margin-top:8px}
</style>
</head>
<body>
<main class="sheet">
  <svg class="bands" viewBox="0 0 824 1067" aria-hidden="true">
    <g fill="none" stroke-width="23">
      <path d="M0 229 C 380 229, 580 222, 824 98" stroke="var(--blue-soft)"/>
      <path d="M0 252 C 380 252, 590 245, 824 121" stroke="var(--green-deep)"/>
      <path d="M0 275 C 380 275, 600 268, 824 144" stroke="var(--gold)"/>
      <path d="M0 298 C 380 298, 610 291, 824 167" stroke="var(--coral)"/>
    </g>
    <g fill="none" stroke-width="22">
      <path d="M0 590 C 100 520, 150 455, 300 452 L 824 450" stroke="var(--coral)"/>
      <path d="M0 612 C 100 542, 160 477, 310 474 L 824 472" stroke="var(--gold)"/>
      <path d="M0 634 C 100 564, 170 499, 320 496 L 824 494" stroke="var(--green-deep)"/>
      <path d="M0 656 C 100 586, 180 521, 330 518 L 824 516" stroke="var(--blue-soft)"/>
    </g>
  </svg>

  <p class="brand-name">Copper Hollow<br>Graphics</p>
  <p class="kit-title">SAMPLE MERCH KIT</p>
  <div class="badge"></div>
  <p class="est">Est. 1979</p>

  <p class="spec model"><b>Model:</b> CHG Shop T-shirts</p>
  <p class="spec series"><b>Series:</b> Summer/Fall 2025 Collection</p>
  <p class="warning"><span>WARNING:</span>These shirts may cause increased shop morale, envy from competitors, and a high volume of customer demand.</p>

  <div class="garment-shadow" style="left:63px"></div>
  <div class="garment-shadow" style="left:324px"></div>
  <div class="garment-shadow" style="left:584px"></div>
  <div class="garment olive" role="img" aria-label="Olive t-shirt printed with a custom vehicle shop design"></div>
  <div class="garment black" role="img" aria-label="Black t-shirt printed with an off-road truck design"></div>
  <div class="garment blue" role="img" aria-label="Royal blue t-shirt printed with a classic muscle car sunset design"></div>

  <section class="kit-contents">
    <h2>MERCH KIT<br>CONTENTS:</h2>
    <ol>
      <li>1. Custom Shop T-shirt</li>
      <li>2. Additional Sample Shirt</li>
      <li>3. CHG Ink Pen</li>
    </ol>
  </section>

  <section class="order-steps">
    <h2>HOW TO START AN ORDER</h2>
    <p class="sub">/ Creating T-shirts is quick and easy</p>
    <div class="step">
      <svg width="20" height="30" viewBox="0 0 20 30" fill="none" stroke="#fff" stroke-width="1.3"><circle cx="10" cy="8" r="7"/><path d="M10 19v8M7 24l3 3 3-3"/></svg>
      <strong>1.CHOOSE YOUR RIDE</strong>Send us a picture, or let us know the make and model of the vehicle you would like featured on your apparel.
    </div>
    <div class="step">
      <svg width="20" height="30" viewBox="0 0 20 30" fill="none" stroke="#fff" stroke-width="1.3"><path d="M4 3l4-1h4l4 1 3 4-3 2v7H5V9L2 7z"/><path d="M10 19v8M7 24l3 3 3-3"/></svg>
      <strong>2. PICK YOUR GEAR</strong>We will help you choose your t-shirts, sweatshirts or other apparel items and determine sizes and quantities.
    </div>
    <div class="step">
      <svg width="20" height="20" viewBox="0 0 20 20" fill="none" stroke="#fff" stroke-width="1.3"><path d="M3 3l14 14M17 3L3 17"/></svg>
      <strong>3. WE CUSTOMIZE</strong>We make the magic happen and our team of expert artists will design your shirts and get a proof out to you.<br>Upon order approval your order will go into production.
    </div>
  </section>

  <section class="about">
    <h2>ABOUT US:</h2>
    <p>Copper Hollow Graphics is a second-generation screen printing company in Millbrook, VA. For over 45 years, we've specialized in high-quality custom apparel and merchandise.</p>
    <p><span class="fine">THE FINE PRINT:</span>Please send high-resolution photos of vehicles. When sending additional logos, please send vector images. Note that our shop minimum is 24 pieces for one-color prints and 100 pieces for full-color screen print. We also promise accurate, quality work.</p>
  </section>

  <section class="contact">
    <p class="pill">CONTACT US TODAY!</p>
    <p class="phone">540-555-0183</p>
    <p class="web">chgtees.com</p>
  </section>
</main>
</body>
</html>
```